Australian Trucking Company Requires Professional Looking Stationary

We require a professional looking stationary design that incorporates our newly designed logo.

Our business, called "Brell Haulage Contracting", provides contracting work, transport and logistics to business in Western Australia particularly with links to the mining sector.

We are a small business looking to expand and our new logo and our new stationary will help develop our brand image in our market place.

Target Market(s)

Businesses and Corporation with links to the Mining Sector

Industry/Entity Type

Small Business

Requirements
Must have
• The letterhead must have the following details:
The new logo

Text saying: "Brell Holdings Pty Ltd (ACN 582 316 907) ATF The Brell Discretionary Trust T/AS"
"ABN 71 834 209 553"
Address "P.O Box 817 Wattlegrove WA, 6958"
Phone: 08 9352 7140
Email: brellhaul@mailbox-example.com.au

The text on the letterhead should be editable as the details are likely to change in the near future. Provision should be made for a website address all though one isn't available at the moment.

The styling, layout and font text is entirely up to the designer.

```html
<!DOCTYPE html>
<html lang="en">
<head>
<meta charset="utf-8">
<title>Brell Haulage Contracting – Business Card</title>
<link rel="stylesheet" href="https://fonts.googleapis.com/css2?family=Roboto:wght@400;700;900&display=swap">
<style>
  :root {
    --page: #e9e7e4;
    --card: #ffffff;
    --red: #a51d24;
    --red-bright: #d4222b;
    --grey: #5a5a5a;
    --grey-soft: #8a8a8a;
  }
  html, body {
    margin: 0;
    padding: 0;
    width: 1200px;
    height: 1200px;
    overflow: hidden;
    background: var(--page);
    font-family: "Roboto", Arial, sans-serif;
  }
  .canvas { position: relative; width: 1200px; height: 1200px; }
  .card {
    position: absolute;
    width: 840px;
    height: 480px;
    background: var(--card);
    box-shadow: 0 2px 10px rgba(0,0,0,0.18);
  }
  .card--front { left: 84px; top: 78px; }
  .card--back { left: 284px; top: 650px; }

  /* Front */
  .brand {
    position: absolute;
    left: 40px;
    top: 62px;
    margin: 0;
    color: var(--red);
    font-weight: 900;
    font-size: 50px;
    line-height: 56px;
    text-transform: uppercase;
  }
  .brand__mark {
    display: inline-block;
    width: 26px; height: 26px;
    background: var(--grey);
    border-radius: 50%;
    margin-right: 14px;
    vertical-align: 6px;
  }
  .rule {
    position: absolute;
    top: 276px;
    height: 2px;
    background: var(--red-bright);
  }
  .rule--left { left: 0; width: 565px; }
  .rule--right { left: 778px; width: 62px; }
  .person {
    position: absolute;
    right: 78px;
    top: 254px;
    text-align: right;
  }
  .person__name {
    color: var(--red);
    font-weight: 700;
    font-size: 31px;
    line-height: 40px;
  }
  .person__title {
    color: var(--red);
    font-size: 24px;
    letter-spacing: 2px;
    margin-top: 2px;
  }
  .contacts {
    position: absolute;
    right: 70px;
    top: 340px;
    margin: 0;
    padding: 0;
    list-style: none;
    text-align: right;
  }
  .contacts li {
    color: var(--red);
    font-size: 21px;
    line-height: 33.5px;
    display: flex;
    justify-content: flex-end;
    align-items: center;
    gap: 20px;
  }
  .contacts svg { width: 18px; height: 18px; fill: var(--red); flex: none; }

  /* Back */
  .back-brand {
    position: absolute;
    left: 0; right: 0;
    top: 150px;
    text-align: center;
    color: var(--grey);
    font-weight: 900;
    font-size: 40px;
    text-transform: uppercase;
  }
  .back-brand__mark {
    display: inline-block;
    width: 30px; height: 30px;
    background: var(--grey);
    border-radius: 50%;
    margin-right: 16px;
    vertical-align: 2px;
  }
  .legal {
    position: absolute;
    left: 0; right: 0;
    top: 358px;
    text-align: center;
    color: var(--red);
    font-size: 19px;
    line-height: 37px;
  }
  .web {
    position: absolute;
    left: 0; right: 0;
    top: 432px;
    text-align: center;
    font-size: 30px;
    letter-spacing: 2px;
    color: var(--grey);
  }
  .web__name { color: var(--red); font-weight: 900; }
</style>
</head>
<body>
<div class="canvas">

  <section class="card card--front">
    <h1 class="brand"><span class="brand__mark"></span>Brell<br>Haulage<br>Contracting</h1>

    <div class="rule rule--left"></div>
    <div class="rule rule--right"></div>

    <div class="person">
      <div class="person__name">Your Name</div>
      <div class="person__title">Title</div>
    </div>

    <ul class="contacts">
      <li>08 9352 7140
        <svg viewBox="0 0 20 20"><circle cx="10" cy="10" r="8.5" fill="none" stroke="#a51d24" stroke-width="1.5"/><path d="M7 5.5c-1 1-1.3 3 .5 5.8s3.7 3.8 5 3.4l.8-1.6-2-1.2-.9.9c-.8-.3-2-1.6-2.4-2.5l.8-.9-1-2.2z"/></svg>
      </li>
      <li>brellhaul@mailbox-example.com.au
        <svg viewBox="0 0 20 20"><rect x="2" y="5" width="16" height="11"/><path d="M2 5l8 6 8-6" fill="none" stroke="#fff" stroke-width="1.5"/></svg>
      </li>
      <li>www.brellhaulage.com
        <svg viewBox="0 0 20 20"><g fill="none" stroke="#a51d24" stroke-width="1.3"><circle cx="10" cy="10" r="8"/><ellipse cx="10" cy="10" rx="3.5" ry="8"/><path d="M2 10h16M3.5 6h13M3.5 14h13"/></g></svg>
      </li>
      <li>P.O Box 817 Wattlegrove WA, 6958
        <svg viewBox="0 0 20 20"><path d="M10 2l9 8h-3v8h-4v-5H8v5H4v-8H1z"/></svg>
      </li>
    </ul>
  </section>

  <section class="card card--back">
    <div class="back-brand"><span class="back-brand__mark"></span>Brell Haulage</div>
    <div class="legal">
      Brell Holdings Pty Ltd (ACN 582 316 907) ATF The Brell Discretionary Trust T/AS<br>
      ABN 71 834 209 553
    </div>
    <div class="web">www.<span class="web__name">brellhaulage</span>.com</div>
  </section>

</div>
</body>
</html>
```